Counseling Practice Business Card

I need a professional looking business card incorporating my new logo that was just completed. Card needs to incorporate my name and title, description of my specialty, my address, my phone number, my fax number, my email and my website URL. I need to be able to choose design on/with different paper colors and textures.
I do not have a lot of business card ideas so I am open to anything but I want bold,sharp, clear card without additional designs other than my logo (see attached file info). I am open to different color backgrounds or paper colors including black. I do not like traditional brackets around area codes in phone number or dashes between numbers in phone number. Am open to other ways of presenting including periods between numbers as appropriate. I do not know enough to know what I like yet but I want card to coordinate and work together with my logo. My practice emphasizes natural mental health interventions so any use of color (with background paper color or the blue and green in my logo) that elicits nature is nice. In addition to black, any natural brown or wood looking background might be desirable also. Most of the offerings so far look very similar and boring.

Target Market(s)

Potential therapy clients and other professionals

Contact Information for Business Card

Card information:
Gerald M. Whitcombe, Ph.D.
Licensed Clinical Psychologist
Integrative Health Coach
4812 Marlowe Ridge Blvd SE
Suite 310
Alder Bend, GA 30418
(770) 415-2983 phone
(770) 581-4096 fax
drgeraldwhitcombe@quillmarsh.net
brightfernwellness.net

Font styles to use
Serif
Sans Serif
Other font styles liked:
• anything that you think looks crisp, clear and easily readable

Requirements
Must have
• Any color used should coordinate with my logo design (see attached files).
• Card should be printed horizontally so top and bottom are longest sides of rectangle.
• Background color or paper color should complement and highlight logo. Do not like a white background. black, grey, brown or any color my logo would blend well with.
Nice to have
• I would like designer to utilize color to highlight letters/name or phone-fax-web symbols.
• Bottom edge of card could be highlighted if appropriate to an idea.
Should not have
• I would NOT want the card to have a pure white background at all.
• No clear cards.
• Cards should be oriented with long sides on bottom and top, NOT sides. DO NOT LIKE THIS THIN TALL ORIENTATION.

```html
<!DOCTYPE html>
<html lang="en">
<head>
<meta charset="utf-8">
<title>Brightfern Wellness – Business Card</title>
<link href="https://fonts.googleapis.com/css2?family=Roboto:wght@300;400;500&family=Roboto+Condensed:wght@500&display=swap" rel="stylesheet">
<style>
  :root {
    --backdrop: #d8d3cb;
    --card: #141517;
    --brand-blue: #2a6fb3;
    --brand-green: #0e6b35;
    --band-green: #0d6a34;
    --text-light: #d6d6d6;
    --text-band: #c9d6cc;
  }
  * { margin: 0; padding: 0; box-sizing: border-box; }
  html, body { width: 1200px; height: 960px; overflow: hidden; }
  body {
    background: var(--backdrop);
    position: relative;
    font-family: "Roboto", Arial, sans-serif;
  }
  .card {
    position: absolute;
    width: 600px;
    height: 343px;
    background: var(--card);
    box-shadow: 0 3px 8px rgba(0,0,0,0.25);
    overflow: hidden;
  }
  .card--front { left: 314px; top: 113px; }
  .card--back { left: 311px; top: 472px; }

  .brand {
    position: absolute;
    display: flex;
    align-items: center;
    gap: 10px;
    color: var(--brand-blue);
    font-family: "Roboto", Arial, sans-serif;
    font-weight: 500;
    white-space: nowrap;
  }
  .brand__dot {
    border-radius: 50%;
    background: var(--brand-green);
    flex: none;
  }
  .card--front .brand { left: 32px; top: 58px; font-size: 30px; }
  .card--front .brand__dot { width: 22px; height: 22px; }
  .card--back .brand {
    left: 0; right: 0; top: 138px;
    justify-content: center;
    font-size: 44px;
  }
  .card--back .brand__dot { width: 32px; height: 32px; }

  .contact {
    position: absolute;
    left: 32px;
    top: 183px;
    list-style: none;
    color: var(--text-light);
    font-size: 14px;
    font-weight: 300;
    line-height: 19px;
  }
  .contact__item { display: flex; align-items: center; gap: 8px; white-space: nowrap; }
  .contact__icon { width: 13px; height: 13px; flex: none; fill: var(--brand-blue); }
  .address {
    position: absolute;
    left: 35px;
    top: 263px;
    color: var(--text-light);
    font-size: 14px;
    font-weight: 300;
    line-height: 19px;
    font-style: normal;
    white-space: nowrap;
  }

  .person {
    position: absolute;
    right: 38px;
    top: 209px;
    text-align: right;
    white-space: nowrap;
  }
  .person__name {
    font-family: "Roboto Condensed", "Arial Narrow", sans-serif;
    font-weight: 500;
    font-size: 20px;
    color: var(--brand-blue);
    text-transform: uppercase;
    line-height: 24px;
  }
  .person__title {
    color: var(--brand-green);
    font-size: 15px;
    line-height: 19px;
  }
  .accent-bar {
    position: absolute;
    right: 0;
    top: 209px;
    width: 13px;
    height: 63px;
    background: var(--brand-blue);
  }

  .web-band {
    position: absolute;
    left: 0; right: 0;
    top: 279px;
    height: 30px;
    background: var(--band-green);
    color: var(--text-band);
    font-size: 14px;
    letter-spacing: 4px;
    text-align: center;
    line-height: 30px;
  }
</style>
</head>
<body>

<section class="card card--front" aria-label="Business card front">
  <div class="brand"><span class="brand__dot"></span>Brightfern Wellness</div>

  <ul class="contact">
    <li class="contact__item">
      <svg class="contact__icon" viewBox="0 0 16 16" aria-hidden="true"><path d="M3.5 1.5 6 1l1.5 3.5-1.8 1.2a8 8 0 0 0 4.6 4.6L11.5 8.5 15 10l-.5 2.5c-.3 1.2-1.3 2-2.5 1.9C6.5 14 2 9.5 1.6 4c-.1-1.2.7-2.2 1.9-2.5z"/></svg>
      (770) 415-2983
    </li>
    <li class="contact__item">
      <svg class="contact__icon" viewBox="0 0 16 16" aria-hidden="true"><rect x="4" y="1" width="8" height="4"/><rect x="1" y="6" width="14" height="6" rx="1"/><rect x="4" y="10" width="8" height="5" fill="#e3e3e3"/></svg>
      (770) 581-4096
    </li>
    <li class="contact__item">
      <svg class="contact__icon" viewBox="0 0 16 16" aria-hidden="true"><path d="M1 3h14v10H1z"/><path d="M1.5 3.5 8 9l6.5-5.5" fill="none" stroke="#141517" stroke-width="1.4"/></svg>
      drgeraldwhitcombe@quillmarsh.net
    </li>
    <li class="contact__item">
      <svg class="contact__icon" viewBox="0 0 16 16" aria-hidden="true"><circle cx="8" cy="8" r="7"/><path d="M5 4c2 1 1 3 3 3s1 3 3 4M9 2c0 2 2 2 3 1" fill="none" stroke="#141517" stroke-width="1.2"/></svg>
      www.brightfernwellness.net
    </li>
  </ul>

  <address class="address">
    4812 Marlowe Ridge Blvd SE<br>
    Suite 310 Alder Bend, GA 30418
  </address>

  <div class="person">
    <p class="person__name">Gerald M. Whitcombe, Ph.D.</p>
    <p class="person__title">Licensed Clinical Psychologist</p>
    <p class="person__title">Integrative Health Coach</p>
  </div>
  <div class="accent-bar"></div>
</section>

<section class="card card--back" aria-label="Business card back">
  <div class="brand"><span class="brand__dot"></span>Brightfern Wellness</div>
  <div class="web-band">www.brightfernwellness.net</div>
</section>

</body>
</html>
```